Harrow Point Metrics Company Website Design and Coding

We want to redesign our existing website so that it is more visually and functionally appealing to prospective clients and potential job candidates. We would like to keep our current color scheme and implement our current logo as well. We have a high-level idea of website structure that we are thinking of, which is in the attached files. Logo is included as well. The final design would ideally be energy and analytics focused. We will need the new website to be coded as well, please.

Target Market(s)

Energy and utility industry

Industry/Entity Type

Energy/analytics

Coding

Coded - Design and coding required

Number of Pages Required

5+ page

Font styles to use
Sans Serif

Colors
0094D4
00A9DD
6FCCEA
C7EBF8
E9F6FB
F0912C
F2A743
F7CA91
FBE8D2
FDF5EE

Requirements
Must have
• Consistent color scheme- please use the one that we provided. We need an overview, a home page, and our core services. A separate job application page. Logo must be incorporated. We would like e "Meet our Team" page. Please include all of the content that is listed in our attachments.
Nice to have
• Movement
Should not have
• No music, no cartoons/animation, no pictures of a chalkboard

```html
<!DOCTYPE html>
<html lang="en">
<head>
<meta charset="utf-8">
<title>Harrow Point Metrics — Data Driven Research &amp; Insights</title>
<link href="https://fonts.googleapis.com/css2?family=Baloo+2:wght@500;600;700&family=Nunito:wght@400;600;700&display=swap" rel="stylesheet">
<style>
:root{
  --blue:#0094D4;
  --blue-2:#00A9DD;
  --blue-3:#6FCCEA;
  --blue-4:#C7EBF8;
  --blue-5:#E9F6FB;
  --orange:#F0912C;
  --orange-2:#F2A743;
  --orange-deep:#E07A1F;
  --orange-3:#F7CA91;
  --ink:#1d1d1f;
  --muted:#666;
  --night:#0b1020;
}
*{box-sizing:border-box;margin:0;padding:0}
html,body{width:1200px;height:4792px;overflow:hidden}
body{position:relative;font-family:"Nunito",sans-serif;color:var(--ink);background:#fff}
.abs{position:absolute}

/* header */
.site-header{position:absolute;left:0;top:0;width:1200px;height:100px;background:#fff}
.brand{position:absolute;left:48px;top:24px;display:flex;align-items:center;gap:12px}
.brand-dot{width:40px;height:40px;border-radius:50%;background:var(--blue-4);border:3px solid var(--blue)}
.brand-name{font-family:"Baloo 2",sans-serif;font-weight:500;font-size:27px;color:var(--blue);line-height:1}
.brand-tag{font-size:9.5px;letter-spacing:2.4px;color:var(--blue-2);margin-top:4px}
.main-nav{position:absolute;left:508px;top:36px;display:flex;gap:36px;font-size:16px}
.main-nav a{color:var(--ink);text-decoration:none}
.main-nav a.current{color:var(--blue);font-weight:700;text-decoration:underline;text-underline-offset:5px}
.btn{display:inline-flex;align-items:center;justify-content:center;border-radius:30px;font-weight:700;text-decoration:none}
.btn-contact{position:absolute;left:960px;top:26px;width:128px;height:50px;background:var(--orange);color:#1d1d1f;font-size:15px;box-shadow:0 4px 10px rgba(0,0,0,.18)}

.sub-nav{position:absolute;left:0;top:100px;width:1200px;height:70px;background:linear-gradient(90deg,var(--blue),var(--blue-2));display:flex;align-items:center;padding-left:98px;gap:46px;font-size:14.5px;color:#fff}

/* hero */
.hero{position:absolute;left:0;top:170px;width:1200px;height:640px;overflow:hidden}
.hero-bg{position:absolute;inset:0;background:
  radial-gradient(ellipse at 85% 40%,#3c8ff0 0%,rgba(47,111,216,.6) 18%,rgba(20,58,140,0) 45%),
  radial-gradient(ellipse at 55% 30%,rgba(230,120,60,.35) 0%,rgba(0,0,0,0) 30%),
  linear-gradient(100deg,#060b1f 0%,#0d1d52 45%,#143a8c 75%,#0a1a44 100%)}
.hero-title{position:absolute;left:113px;top:112px;font-family:"Baloo 2",sans-serif;font-weight:600;font-size:54px;line-height:64px;color:#fff}
.hero-tag{position:absolute;left:113px;top:256px;font-size:15px;letter-spacing:3px;color:#fff;font-weight:600}
.btn-hero{position:absolute;left:113px;top:302px;width:150px;height:58px;background:var(--orange);color:#1d1d1f;font-size:19px;font-weight:600}

/* section titles */
.section-title{position:absolute;left:0;width:1200px;text-align:center;font-family:"Baloo 2",sans-serif;font-weight:700;font-size:44px;color:var(--blue);line-height:46px}

/* services */
.service-card{position:absolute;top:955px;width:298px;height:390px;background:#fff;border-radius:6px;box-shadow:0 4px 14px rgba(0,0,0,.12);overflow:hidden;text-align:center;display:flex;flex-direction:column}
.service-card.active{border:2px solid var(--blue-2)}
.service-media{height:200px;flex:none}
.service-card h3{font-size:18px;font-weight:600;margin:16px 18px 6px;line-height:24px}
.service-card.active h3{color:var(--blue);font-weight:700}
.service-card p{font-size:13.5px;line-height:24px;color:var(--muted);margin:0 16px}
.service-card.active p{color:var(--ink)}
.read-more{display:block;margin:auto 0 18px;font-size:15px;font-weight:700;color:var(--ink);text-decoration:underline}
.service-card.active .read-more{color:var(--blue)}

.arrow-prev{position:absolute;width:20px;height:30px}
.arrow-next{position:absolute;width:38px;height:38px}

/* about */
.about{position:absolute;left:0;top:1425px;width:1200px;height:465px;background:linear-gradient(120deg,#0d5fbf 0%,#1282d6 45%,#1a98e0 100%)}
.about-media{position:absolute;left:0;top:0;width:540px;height:465px;background:
  radial-gradient(ellipse at 50% 75%,rgba(120,200,255,.55) 0%,rgba(31,120,232,0) 40%),
  radial-gradient(circle at 45% 45%,#2a8cf0 0%,#0f4fb3 40%,#0a2f7a 70%,rgba(13,95,191,0) 100%)}
.band-title{font-family:"Baloo 2",sans-serif;font-weight:700;font-size:44px;line-height:48px;color:#fff}
.band-text{font-size:14.5px;line-height:26px;color:#fff}
.btn-light{background:#fff3ea;color:#1d1d1f;font-size:19px;font-weight:600;box-shadow:0 4px 10px rgba(0,0,0,.2)}

/* research */
.research-card{position:absolute;top:2028px;height:422px;border:2px solid var(--blue);border-radius:12px;background:#fff;padding:8px}
.research-media{height:336px;border-radius:10px}
.research-card h3{font-size:17px;font-weight:600;margin:12px 8px 4px}
.research-card p{font-size:13.5px;margin:0 8px;color:#333}

/* newsletter */
.newsletter{position:absolute;left:0;top:2514px;width:1200px;height:366px;background:linear-gradient(180deg,var(--orange-deep),#d86f16)}
.newsletter-text{position:absolute;left:210px;width:780px;top:132px;text-align:center;font-size:14.5px;line-height:26px;color:#fff}
.subscribe-form{position:absolute;left:218px;top:224px;width:764px;height:70px;background:#fff;border-radius:35px;overflow:hidden}
.subscribe-form span{position:absolute;left:36px;top:24px;font-size:15px;font-weight:600}
.subscribe-btn{position:absolute;right:0;top:0;width:226px;height:70px;background:var(--blue);color:#111;font-weight:700;font-size:15px;display:flex;align-items:center;justify-content:center;letter-spacing:.5px}

/* case studies */
.case-card{position:absolute;top:3035px;width:226px;height:272px;border:1px solid #cfcfcf;border-radius:10px;background:#fff;padding:8px;text-align:center}
.case-media{height:196px;border-radius:8px}
.case-card h3{font-size:14.5px;font-weight:600;line-height:20px;margin-top:9px}

/* careers */
.careers{position:absolute;left:0;top:3372px;width:1200px;height:463px;background:linear-gradient(100deg,#0a4ea8 0%,#1572c9 50%,#0b3f93 100%)}
.careers-media{position:absolute;left:700px;top:0;width:500px;height:463px;background:
  radial-gradient(circle at 58% 48%,#0b3f93 0%,#0b3f93 14%,#3fc3f0 17%,#1a7fd4 30%,#0c4ea9 55%,rgba(11,63,147,0) 80%)}

/* team */
.team-card{position:absolute;top:3995px;width:183px;height:230px;border:2px solid var(--blue);border-radius:4px;background:#fff;text-align:center}
.team-photo{position:absolute;left:33px;top:-22px;width:116px;height:116px;border-radius:50%;background:linear-gradient(160deg,#e6e2dd,#b8b0a8);border:4px solid #fff}
.team-card h3{position:absolute;top:112px;width:100%;font-size:18px;font-weight:400;color:var(--blue)}
.team-card p{position:absolute;top:143px;width:100%;font-size:13px;color:#555}
.team-link{position:absolute;left:75px;top:174px;width:32px;height:32px;border-radius:50%;background:var(--blue)}

/* footer */
.footer{position:absolute;left:0;top:4260px;width:1200px;height:532px}
.foot-col{position:absolute;top:208px;color:#fff}
.foot-col h4{font-family:"Baloo 2",sans-serif;font-weight:600;font-size:22px;margin-bottom:10px}
.foot-col li{list-style:none;font-size:14px;line-height:34px}
.foot-col li::before{content:"» "}
.contact-row{display:flex;align-items:flex-start;gap:14px;font-size:14px;line-height:26px;margin-bottom:14px}
.contact-icon{flex:none;width:30px;height:30px;border-radius:50%;background:var(--orange);display:flex;align-items:center;justify-content:center}
.foot-brand{position:absolute;left:810px;top:210px;width:280px;color:#fff}
.foot-brand .brand-name{color:#fff;font-size:23px}
.foot-brand p{font-size:12.5px;line-height:23px;margin-top:20px}
.foot-rule{position:absolute;left:110px;top:452px;width:980px;height:1px;background:#444}
.copyright{position:absolute;left:110px;top:484px;font-size:13px;color:#fff}
.social{position:absolute;left:922px;top:480px;display:flex;gap:18px}
.social span{width:28px;height:28px;border-radius:50%;background:var(--orange)}
</style>
</head>
<body>

<header class="site-header">
  <div class="brand">
    <div class="brand-dot"></div>
    <div>
      <div class="brand-name">Harrow Point Metrics</div>
      <div class="brand-tag">DATA DRIVEN RESEARCH AND INSIGHTS</div>
    </div>
  </div>
  <nav class="main-nav">
    <a class="current" href="#">Home</a><a href="#">Core Services</a><a href="#">About</a><a href="#">Our Work</a><a href="#">Blog</a>
  </nav>
  <a class="btn btn-contact" href="#">Contact Us</a>
</header>

<nav class="sub-nav">
  <span>Forecasting &amp; Predictive</span><span>Analytics</span><span>T&amp;D planning</span><span>Evalution</span><span>Pilot &amp; Emerging Tech</span><span>Support</span><span>Our Team</span><span>More ▾</span>
</nav>

<section class="hero">
  <div class="hero-bg" role="img" aria-label="Hand pointing a stylus at a tablet showing energy analytics dashboards"></div>
  <h1 class="hero-title">Welcome To Harrow Point<br>Metrics</h1>
  <div class="hero-tag">Data Driven Research &amp; Insights</div>
  <a class="btn btn-hero" href="#">Get Started</a>
  <svg class="abs" style="left:0;top:0" width="1200" height="640" viewBox="0 0 1200 640">
    <path d="M0 470 Q 520 720 1200 430 L1200 640 L0 640 Z" fill="#fff"/>
    <path d="M70 500 Q 560 740 1200 470" fill="none" stroke="#F0912C" stroke-width="6"/>
  </svg>
</section>

<h2 class="section-title" style="top:880px">Our Services</h2>

<svg class="arrow-prev" style="left:40px;top:1146px" viewBox="0 0 20 30"><path d="M14 6 L6 15 L14 24" fill="none" stroke="#555" stroke-width="2.5"/></svg>

<article class="service-card" style="left:112px">
  <div class="service-media" style="background:radial-gradient(circle at 50% 55%,#3fa0f0,#1b6fd0 40%,#0d3f8c)" role="img" aria-label="Gears and charts illustrating predictive analytics"></div>
  <h3>Predictive Analytics and Forecasting</h3>
  <p>Distributed energy resource integration into planning &amp; operations. Time-varying pricing analysis</p>
  <a class="read-more" href="#">Read More</a>
</article>
<article class="service-card active" style="left:452px">
  <div class="service-media" style="height:196px;background:radial-gradient(circle at 50% 50%,#6fccea,#2a8be8 40%,#0b2d6e)" role="img" aria-label="Tablet screens showing planning charts"></div>
  <h3>T&amp;D Planning</h3>
  <p>Location specific, probabilistic forecasting for system, transmission and distribution planning. Expert testimony</p>
  <a class="read-more" href="#">Read More</a>
</article>
<article class="service-card" style="left:793px">
  <div class="service-media" style="background:linear-gradient(180deg,#f2f1ee,#d8d5d0 55%,#6d6a66)" role="img" aria-label="Laptops and monitors on a desk showing reports"></div>
  <h3>Pilot &amp; Emerging Tech Support</h3>
  <p>Design and implementation of pilots and controlled deployments Pilots generally designed to</p>
  <a class="read-more" href="#">Read More</a>
</article>

<svg class="arrow-next" style="left:1132px;top:1140px" viewBox="0 0 38 38"><circle cx="19" cy="19" r="19" fill="#111"/><path d="M16 11 L24 19 L16 27" fill="none" stroke="#fff" stroke-width="3"/></svg>

<section class="about">
  <div class="about-media" role="img" aria-label="Laptop with glowing analytics charts"></div>
  <h2 class="band-title abs" style="left:610px;top:50px;width:480px">About Harrow Point Metrics</h2>
  <p class="band-text abs" style="left:540px;top:146px;width:540px">Harrow Point Metrics was formed in 2016 to help utilities and regulatory agencies navigate the technical, economic, and policy challenges of building a smarter and cleaner energy future.</p>
  <p class="band-text abs" style="left:540px;top:250px;width:540px">Through cutting edge research design and analysis methods we provide DSM program administrators with data-driven insights into how various technologies and interventions affect the way homes and businesses use energy.</p>
  <a class="btn btn-light abs" style="left:540px;top:350px;width:150px;height:60px" href="#">Read More</a>
</section>

<h2 class="section-title" style="top:1946px">Research and Analysis</h2>

<article class="research-card" style="left:112px;width:655px">
  <div class="research-media" style="background:radial-gradient(ellipse at 60% 65%,#2f7ff0 0%,#1d4fb8 35%,#0b1540 80%)" role="img" aria-label="Rising blue bar chart on a dark background"></div>
  <h3>Journal Articles and Conference Presentations</h3>
  <p>Links to relevant published journal articles and conference presentations</p>
</article>
<article class="research-card" style="left:787px;width:301px">
  <div class="research-media" style="background:radial-gradient(ellipse at 50% 55%,#4fd0f0 0%,#1b8fb8 30%,#0a2236 80%)" role="img" aria-label="Server room corridor with blue lighting"></div>
  <h3>Published Reports</h3>
  <p>Links to published reports</p>
</article>

<section class="newsletter">
  <h2 class="section-title" style="top:62px;color:#fff">Join Our Newsletter</h2>
  <p class="newsletter-text">Harrow Point Metrics (HPM) was formed in 2016 to help utilities and regulatory agencies navigate the technical, economic, and policy challenges of building a smarter and cleaner energy future.Our research focuses on impact analysis as well as predictive and causal analytics.</p>
  <div class="subscribe-form"><span>Enter The Email</span><div class="subscribe-btn">SUBSCRIBE</div></div>
</section>

<h2 class="section-title" style="top:2930px">Proposed Case Studies for Each<br>Core Service</h2>

<svg class="arrow-prev" style="left:40px;top:3143px" viewBox="0 0 20 30"><path d="M14 6 L6 15 L14 24" fill="none" stroke="#222" stroke-width="2.5"/></svg>

<article class="case-card" style="left:112px">
  <div class="case-media" style="background:radial-gradient(circle at 50% 55%,#3fa0f0,#1b6fd0 40%,#0d3f8c)" role="img" aria-label="Predictive analytics illustration"></div>
  <h3>Predictive Analytics and Forecasting</h3>
</article>
<article class="case-card" style="left:364px">
  <div class="case-media" style="background:radial-gradient(ellipse at 50% 90%,#b04bd0 0%,#3a4fd8 25%,#1a2fa0 50%,#0a0f3a 90%)" role="img" aria-label="Glowing light streams converging"></div>
  <h3>T&amp;D Planning – Northvale Power or Eastridge Utility</h3>
</article>
<article class="case-card" style="left:611px">
  <div class="case-media" style="background:radial-gradient(circle at 60% 40%,#3a8fd0,#1a4f86 40%,#081a33)" role="img" aria-label="Network of connected points"></div>
  <h3>Evaluation – Coastline Electric? Bayridge Gas &amp; Electric? Different state</h3>
</article>
<article class="case-card" style="left:861px">
  <div class="case-media" style="background:radial-gradient(circle,#e0459b,#6a2aa0 45%,#1a1a6a 75%,#0b0c2a)" role="img" aria-label="Abstract swirling lines"></div>
  <h3>Pilot &amp; Emerging Tech Support</h3>
</article>

<svg class="arrow-next" style="left:1132px;top:3139px" viewBox="0 0 38 38"><circle cx="19" cy="19" r="19" fill="#111"/><path d="M16 11 L24 19 L16 27" fill="none" stroke="#fff" stroke-width="3"/></svg>

<section class="careers">
  <div class="careers-media" role="img" aria-label="Digital hand holding a ring of analytics icons"></div>
  <h2 class="band-title abs" style="left:180px;top:68px">Our Careers</h2>
  <p class="band-text abs" style="left:110px;top:134px;width:555px">At HPM, we are driven to help create a smarter and cleaner energy future, and we are always looking for talented professionals who share our passion for achieving this goal. We are a transparent organization where you will have the opportunity to work directly with our senior energy experts.</p>
  <p class="band-text abs" style="left:110px;top:262px;width:555px">Our employees get to work on a wide variety of projects and develop new skills so that they are well equipped to interact with our clients find effective ways to solve our clients' problems.</p>
  <a class="btn btn-light abs" style="left:110px;top:356px;width:148px;height:60px" href="#">Read More</a>
</section>

<h2 class="section-title" style="top:3900px">Our Team</h2>

<article class="team-card" style="left:108px"><div class="team-photo" role="img" aria-label="Portrait of a team member"></div><h3>John Doe</h3><p>Company name</p><span class="team-link"></span></article>
<article class="team-card" style="left:374px"><div class="team-photo" role="img" aria-label="Portrait of a team member"></div><h3>John Doe</h3><p>Company name</p><span class="team-link"></span></article>
<article class="team-card" style="left:640px"><div class="team-photo" role="img" aria-label="Portrait of a team member"></div><h3>John Doe</h3><p>Company name</p><span class="team-link"></span></article>
<article class="team-card" style="left:905px"><div class="team-photo" role="img" aria-label="Portrait of a team member"></div><h3>John Doe</h3><p>Company name</p><span class="team-link"></span></article>

<footer class="footer">
  <svg class="abs" style="left:0;top:0" width="1200" height="532" viewBox="0 0 1200 532">
    <path d="M0 200 Q 600 -20 1200 70 L1200 532 L0 532 Z" fill="#F0912C"/>
    <path d="M0 212 Q 620 10 1200 84 L1200 532 L0 532 Z" fill="#000"/>
  </svg>
  <div class="foot-col" style="left:110px">
    <h4>Quick Link</h4>
    <ul><li>Home</li><li>About</li><li>Services</li><li>Testimonials</li><li>Contact us</li></ul>
  </div>
  <div class="foot-col" style="left:322px">
    <h4>Help Link</h4>
    <ul><li>FAQ</li><li>Terms of use</li><li>Privacy Policy</li><li>Support Links</li><li>Conditions</li></ul>
  </div>
  <div class="foot-col" style="left:540px;width:240px">
    <h4>Contact us</h4>
    <div class="contact-row"><span class="contact-icon"><svg width="14" height="18" viewBox="0 0 14 18"><path d="M7 1 C3.5 1 1 3.5 1 7 C1 11 7 17 7 17 C7 17 13 11 13 7 C13 3.5 10.5 1 7 1 Z" fill="#fff"/><circle cx="7" cy="7" r="2.2" fill="#F0912C"/></svg></span><span>Harrow Point Metrics<br>United States</span></div>
    <div class="contact-row"><span class="contact-icon"><svg width="16" height="16" viewBox="0 0 16 16"><path d="M3 1 L6 1 L7 5 L5 6.5 C6 8.8 7.2 10 9.5 11 L11 9 L15 10 L15 13 C15 14 14 15 13 15 C6.5 15 1 9.5 1 3 C1 2 2 1 3 1 Z" fill="#fff"/></svg></span><span>+1 555 014 2290</span></div>
    <div class="contact-row"><span class="contact-icon"><svg width="16" height="12" viewBox="0 0 16 12"><rect x="0.5" y="0.5" width="15" height="11" rx="1.5" fill="#fff"/><path d="M1 1 L8 7 L15 1" fill="none" stroke="#F0912C" stroke-width="1.5"/></svg></span><span>info@harrowpointmetrics.com</span></div>
  </div>
  <div class="foot-brand">
    <div style="display:flex;align-items:center;gap:10px">
      <div class="brand-dot" style="width:34px;height:34px;background:#fff;border-color:#fff"></div>
      <div class="brand-name">Harrow Point Metrics</div>
    </div>
    <p>Harrow Point Metrics (HPM) was formed in 2016 to help utilities and regulatory agencies navigate the technical, economic, and policy challenges of building a smarter and cleaner energy future.</p>
  </div>
  <div class="foot-rule"></div>
  <div class="copyright">Copyrights@2022.Harrow Point Metrics.All Rights Reserved</div>
  <div class="social"><span></span><span></span><span></span><span></span></div>
</footer>

</body>
</html>
```